"Harbor Builders" is a residential building company and needs a new business card design and may re

We would like a redesign based on the existing logo, and would like to see a new font as well. We are bespoke home builders who build sustainable energy efficient homes.

Industry/Entity Type

Construction

Contact Information for Business Card

Business card size 40mm x 90mm

Colors

Designer to choose colors to be used in the design.

```html
<!DOCTYPE html>
<html lang="en">
<head>
<meta charset="utf-8">
<title>Harbor Builders — Business Card</title>
<link href="https://fonts.googleapis.com/css2?family=Arimo:wght@400;700&display=swap" rel="stylesheet">
<style>
  :root {
    --backdrop: #e9e4dd;
    --card-navy: #1e2433;
    --accent-tan: #c7a38a;
    --shadow: rgba(30, 36, 51, 0.18);
  }
  * { margin: 0; padding: 0; box-sizing: border-box; }
  html, body {
    width: 1200px;
    height: 800px;
    overflow: hidden;
    background: var(--backdrop);
    font-family: "Arimo", Arial, sans-serif;
  }
  .canvas {
    width: 1200px;
    height: 800px;
    display: flex;
    align-items: center;
    justify-content: center;
    gap: 60px;
  }
  .card {
    width: 520px;
    height: 318px;
    background: var(--card-navy);
    color: var(--accent-tan);
    box-shadow: 0 10px 30px var(--shadow);
    position: relative;
  }
  /* Front */
  .card-front {
    display: flex;
    align-items: center;
    justify-content: center;
    gap: 26px;
  }
  .brand-mark {
    width: 72px;
    height: 72px;
    background: var(--accent-tan);
  }
  .brand-name {
    font-weight: 400;
    font-size: 40px;
    line-height: 1.12;
    letter-spacing: 1.5px;
  }
  /* Back */
  .card-back { padding: 34px 36px; }
  .holder-name {
    position: absolute;
    left: 36px;
    top: 34px;
    font-weight: 700;
    font-size: 30px;
    line-height: 1.2;
    letter-spacing: 0.5px;
  }
  .contact-list {
    position: absolute;
    left: 262px;
    top: 90px;
    font-size: 15px;
    line-height: 1.35;
    letter-spacing: 0.4px;
    list-style: none;
  }
  .contact-group + .contact-group { margin-top: 14px; }
</style>
</head>
<body>
  <main class="canvas">
    <section class="card card-front" aria-label="Business card front">
      <span class="brand-mark" aria-hidden="true"></span>
      <p class="brand-name">Harbor<br>Builders</p>
    </section>

    <section class="card card-back" aria-label="Business card back">
      <h1 class="holder-name">Daniel<br>Moretti</h1>
      <ul class="contact-list">
        <li class="contact-group">0400 555 018</li>
        <li class="contact-group">daniel@harborbuilders.com.au<br>www.harborbuilders.com.au</li>
        <li class="contact-group">PO Box 2170 Eastgate LPO<br>Bayview WA 6999</li>
        <li class="contact-group">Registration 10482<br>ABN: 42 305 918 766</li>
      </ul>
    </section>
  </main>
</body>
</html>
```